Christmas Collection Candle Label Design

Looking to update our existing Christmas Candle Collection labels. Labels should reflect the overall feel of our brand- www.kelvanoro.ca
Want to include some color elements. Holiday colors added into design but more muted/ earthy tones not vibrant colors . Metallic elements and line art botanical illustration. Fonts should be more align to brand
Scents
Holiday Tree
Candy Cane
Sugar and Spice
Joyeaux Noel

```html
<!DOCTYPE html>
<html lang="en">
<head>
<meta charset="utf-8">
<title>Holiday Tree – Christmas Collection Label</title>
<link rel="stylesheet" href="https://fonts.googleapis.com/css2?family=Libre+Baskerville:wght@400;700&family=Open+Sans:wght@300;400&display=swap">
<style>
  :root {
    --backdrop: #e7e7e7;
    --sage-light: #a4a697;
    --sage-dark: #7b7f70;
    --ink: #232323;
    --ink-soft: #2e2e2e;
    --line-art: rgba(225, 226, 216, 0.35);
  }
  * { box-sizing: border-box; margin: 0; padding: 0; }
  html, body {
    width: 1200px; height: 819px; overflow: hidden;
    background: var(--backdrop);
  }
  .canvas {
    position: relative; width: 1200px; height: 819px;
  }
  .label {
    position: absolute; left: 320px; top: 140px;
    width: 560px; height: 540px;
    background: linear-gradient(90deg, var(--sage-light) 0%, #8f9282 45%, var(--sage-dark) 100%);
    overflow: hidden;
  }
  .botanical-art {
    position: absolute; inset: 0;
    background:
      radial-gradient(ellipse 120px 220px at 300px 150px, var(--line-art), transparent 70%),
      radial-gradient(ellipse 110px 180px at 440px 260px, var(--line-art), transparent 70%),
      radial-gradient(ellipse 120px 110px at 90px 420px, var(--line-art), transparent 70%);
  }
  .brand {
    position: absolute; top: 44px; left: 0; width: 100%;
    text-align: center;
  }
  .brand-dot {
    display: block; width: 6px; height: 6px; margin: 0 auto 8px;
    border-radius: 50%; background: var(--ink-soft);
  }
  .brand-name {
    font-family: "Libre Baskerville", serif; font-weight: 400;
    font-size: 24px; letter-spacing: 0.5px; color: var(--ink-soft);
  }
  .brand-tagline {
    font-family: "Open Sans", sans-serif; font-weight: 400;
    font-size: 6px; letter-spacing: 2.4px; color: var(--ink-soft);
    margin-top: 2px;
  }
  .botanical-note {
    position: absolute; top: 290px; right: 130px;
    font-family: "Open Sans", sans-serif; font-size: 10px;
    color: var(--ink-soft);
  }
  .scent-name {
    position: absolute; top: 308px; right: 116px;
    font-family: "Libre Baskerville", serif; font-weight: 700;
    font-size: 52px; line-height: 1.24; color: var(--ink);
    text-align: right; letter-spacing: 0.5px;
  }
  .scent-name span { display: block; }
  .details {
    position: absolute; left: 112px; top: 446px;
    width: 312px; border-collapse: collapse;
    font-family: "Open Sans", sans-serif; font-weight: 300;
    font-size: 18px; color: var(--ink-soft);
  }
  .details td {
    padding: 2px 10px;
    border-top: 1px solid var(--ink-soft);
    text-align: center; white-space: nowrap;
  }
  .details tr:last-child td { border-bottom: 1px solid var(--ink-soft); }
  .details td + td { border-left: 1px solid var(--ink-soft); }
</style>
</head>
<body>
<main class="canvas">
  <section class="label">
    <div class="botanical-art" role="img" aria-label="Fine line-art botanical petals flowing across the label"></div>
    <header class="brand">
      <span class="brand-dot"></span>
      <div class="brand-name">KELVANORO</div>
      <div class="brand-tagline">PURE PLANT BASED SCENTS</div>
    </header>
    <p class="botanical-note">made with plant based botanical</p>
    <h1 class="scent-name"><span>HOLIDAY</span><span>TREE</span></h1>
    <table class="details">
      <tr><td>13 oz</td><td>Christmas Collection</td></tr>
      <tr><td>kelvanoro</td><td>made in canada</td></tr>
    </table>
  </section>
</main>
</body>
</html>
```